Design a Job Application & CV

I need a design for upcoming job applications that includes a cv. It needs to look as elegant and modern as possible as the application will be send mainly to large corporations and strategy consultancies. I have attached an application that I like for your consideration. One of the more difficult requirements is that it needs to be editable in ms office word for mac/windows.
As stated only the design is part of this project. I will fill in my content later on.
Reason: Dear Designers,
I am going to increase the budget as well as extending the deadline. I am hoping that you can improve upon the design that I have provided in the brief. If you have questions please let me know.
Dear Designers,
Target Market(s)
Human Resources Managers, Senior Consultants and Executives of larger firms
Industry/Entity Type
Office
Requirements
Must have
- 4 Pages including( a cover page, a coverletter page, 2 pages cv)
It should be easy to edit and should be readable by word for mac, i.e. in the *.docx format.
Here is an example of what I like:
http://www.torvenmald.example/applicationexample.pdf
http://www.torvenmald.example/applicationExample.docx
colors that I like are blue, grey, black, white
Nice to have
- icons to indicate sections
Should not have
- invasive cliparts

```html
<!DOCTYPE html>
<html lang="en">
<head>
<meta charset="utf-8">
<title>Coverletter</title>
<link rel="stylesheet" href="https://fonts.googleapis.com/css2?family=Tenor+Sans&display=swap">
<style>
  :root {
    --page-grey: #67686d;
    --header-navy-dark: #16202c;
    --header-navy: #27384a;
    --accent-blue: #1f5f93;
    --accent-blue-light: #3d87c2;
    --silver: #c9ccd1;
    --silver-dark: #8b8f96;
    --title-white: #ffffff;
    --body-text: #dcdcdc;
  }
  * { margin: 0; padding: 0; box-sizing: border-box; }
  html, body {
    width: 848px;
    height: 1200px;
    overflow: hidden;
    background: var(--page-grey);
  }
  .page {
    position: relative;
    width: 848px;
    height: 1200px;
    background: var(--page-grey);
    font-family: "Tenor Sans", "Trebuchet MS", sans-serif;
    color: var(--body-text);
  }
  .page-header {
    position: absolute;
    top: 0;
    left: 0;
    width: 848px;
    height: 170px;
  }
  .header-swoosh {
    position: absolute;
    inset: 0;
    width: 848px;
    height: 170px;
  }
  .page-title {
    position: absolute;
    top: 18px;
    left: 72px;
    font-size: 56px;
    font-weight: 400;
    color: var(--title-white);
    letter-spacing: 0.5px;
  }
  .letter {
    position: absolute;
    top: 196px;
    left: 45px;
    width: 758px;
    font-size: 20.5px;
    line-height: 40.5px;
  }
  .letter-salutation { margin-bottom: 23px; }
  .letter-paragraph {
    text-align: justify;
    hyphens: manual;
    margin-bottom: 41px;
  }
  .letter-paragraph:last-of-type { margin-bottom: 0; }
  .letter-closing,
  .letter-signature { line-height: 32px; }
</style>
</head>
<body>
<main class="page">
  <header class="page-header">
    <svg class="header-swoosh" viewBox="0 0 848 170" aria-hidden="true">
      <defs>
        <linearGradient id="navyFill" x1="0" y1="0" x2="0" y2="1">
          <stop offset="0" stop-color="var(--header-navy)"/>
          <stop offset="1" stop-color="var(--header-navy-dark)"/>
        </linearGradient>
        <linearGradient id="blueBand" x1="0" y1="0" x2="1" y2="0">
          <stop offset="0" stop-color="var(--accent-blue)"/>
          <stop offset="0.7" stop-color="var(--accent-blue-light)"/>
          <stop offset="1" stop-color="var(--accent-blue)"/>
        </linearGradient>
        <linearGradient id="silverLine" x1="0" y1="0" x2="1" y2="0">
          <stop offset="0" stop-color="var(--silver-dark)"/>
          <stop offset="0.5" stop-color="var(--silver)"/>
          <stop offset="1" stop-color="#ffffff"/>
        </linearGradient>
      </defs>
      <path class="silver-line" d="M0 150 C 260 155, 560 130, 848 60 L848 72 C 560 142, 260 166, 0 160 Z" fill="url(#silverLine)"/>
      <path class="blue-band" d="M0 110 C 260 132, 560 108, 848 22 L848 62 C 560 134, 260 152, 0 146 Z" fill="url(#blueBand)"/>
      <path class="navy-band" d="M0 0 H848 V22 C 560 104, 260 126, 0 110 Z" fill="url(#navyFill)"/>
    </svg>
    <h1 class="page-title">Coverletter</h1>
  </header>

  <section class="letter">
    <p class="letter-salutation">Dear Folks</p>
    <p class="letter-paragraph">Lorem ipsum dolor sit amet, consectetur adipiscing elit. Quisque dictum leo quis mauris dictum auctor. Praesent viverra, elit at rutrum fringilla, purus nisi feugiat est, sit amet lobortis magna mauris id nibh. Sed interdum massa non mauris faucibus cursus. Integer at tellus sit amet lacus ultrices ullamcorper. Nunc vel libero dui, sit amet pellentesque ligula. Suspendisse semper, urna.</p>
    <p class="letter-paragraph">Aenean quis nisi arcu, blandit mollis odio. Vestibulum nulla enim, viverra a auctor quis, suscipit rhoncus libero. Donec quis libero vel magna luctus pulvi&shy;nar. Duis eget nulla vel massa commodo semper placerat id leo. Nunc eu leo sed quam hendrerit accumsan. Maecenas eleifend nisi non velit dignissim ut suscipit arcu imperdiet. Phasellus nisi nulla, tincidunt. Proin tincidunt, est sed rhoncus mattis, nunc sem aliquet quam, eget tristique augue dolor vel orci. Vestibulum et tellus dui, vitae sollicitudin sapien. Pellentesque nisi tortor, fauci&shy;bus in mollis non, dignissim et felis.</p>
    <p class="letter-paragraph">Phasellus nisi nulla, tincidunt. Proin tincidunt, est sed rhoncus mattis, nunc sem aliquet quam, eget tristique augue dolor vel orci. Vestibulum et tellus dui, vitae sollicitudin sapien. Pellentesque nisi tortor, faucibus in mollis non, dignissim et felis.</p>
    <p class="letter-closing">Sincerely,</p>
    <p class="letter-signature">Good Looking</p>
  </section>
</main>
</body>
</html>
```